Online media outlet needs a blog and logo

A new online blog platform is being established in the UK. The blog will be very similar in layout to www.quorvel.co. It will need to have a main story slider showing three slides and block tiles beneath the slider for additional tiles.

The blog platform will be called 'Tandrel Brisk' and will also need a professional looking logo design for the name.

The website should be designed in Word Press.

Industry/Entity Type

Media

Logo Text

Tandrel Brisk

Coding

Coded - Design and coding required

Number of Pages Required

3 page

Font styles to use
Other font styles liked:
• Helvetica

Requirements
Must have
• A slider showing three slides. Be similar to Quor V (see previous comment). Be Word Press compatible.

```html
<!DOCTYPE html>
<html lang="en">
<head>
<meta charset="utf-8">
<title>Tandrel Brisk</title>
<link href="https://fonts.googleapis.com/css2?family=Roboto:wght@400;500;700&display=swap" rel="stylesheet">
<style>
:root{
  --blue:#1a87d6;
  --blue-dark:#0f6fb8;
  --ink:#222a33;
  --muted:#7d8690;
  --line:#e4e7ea;
  --page:#f4f5f7;
  --white:#ffffff;
  --night:#111820;
  --nav:#1c1f23;
}
*{box-sizing:border-box;margin:0;padding:0}
html,body{width:1200px;height:2459px;overflow:hidden}
body{font-family:'Roboto',Helvetica,Arial,sans-serif;background:var(--page);color:var(--ink);position:relative}
.abs{position:absolute}

/* hero */
.hero{left:0;top:0;width:1200px;height:541px;
  background:linear-gradient(180deg,#2b3550 0%,#5a5a74 30%,#8a6d5e 55%,#3b3436 72%,#1b1d24 100%)}
.hero-shade{left:0;top:0;width:1200px;height:541px;background:linear-gradient(90deg,rgba(10,12,20,.55),rgba(10,12,20,.1) 60%)}
.brand{left:98px;top:26px;color:var(--white);font-size:30px;font-weight:400;letter-spacing:.2px}
.social-top{left:716px;top:28px;display:flex;align-items:center;gap:10px;color:var(--white);font-size:12px;font-weight:500}
.social-top .ring{width:32px;height:32px;border:1.5px solid var(--white);border-radius:50%}
.social-top .label{margin-right:6px}
.menu{left:1034px;top:34px;color:var(--white);font-size:12px;font-weight:500;display:flex;align-items:center;gap:12px}
.menu-bars{width:22px;display:flex;flex-direction:column;gap:4px}
.menu-bars i{display:block;height:3px;background:var(--white)}
.hero-date{left:98px;top:218px;width:126px;height:36px;border:1.5px solid var(--white);color:var(--white);font-size:12px;display:flex;align-items:center;justify-content:center}
.hero-title{left:98px;top:276px;color:var(--white);font-size:30px;font-weight:700}
.hero-text{left:98px;top:322px;width:458px;color:#e9ecf0;font-size:16px;line-height:24px;text-align:justify}
.hero-by{left:98px;top:384px;color:var(--white);font-size:13px;font-weight:700}
.dots{left:1034px;top:482px;display:flex;gap:12px}
.dots i{width:15px;height:15px;border-radius:50%;border:1.5px solid var(--white)}
.dots i.on{background:var(--blue);border-color:var(--blue)}

/* category nav */
.cat-nav{left:98px;top:541px;width:1003px;height:59px;background:var(--nav);display:flex}
.cat-nav a{flex:1;color:var(--white);text-decoration:none;font-size:12px;font-weight:500;display:flex;align-items:center;justify-content:center;letter-spacing:.3px}
.cat-nav a.active{background:var(--blue);flex:0 0 199px}

/* cards */
.card{background:var(--white);border:1px solid var(--line)}
.card-media{position:absolute;left:0;top:0;width:100%;height:233px}
.date-tag{position:absolute;height:31px;width:144px;background:var(--blue);color:var(--white);font-size:11px;font-weight:500;display:flex;align-items:center;padding-left:26px;clip-path:polygon(0 0,86% 0,100% 100%,0 100%)}
.card-body{position:absolute;left:27px;right:24px}
.card-title{font-size:12.5px;font-weight:700;color:var(--ink);white-space:nowrap}
.card-text{margin-top:9px;font-size:11px;line-height:19px;color:var(--muted)}
.share-dots{display:flex;gap:19px;margin-top:16px}
.share-dots i{width:9px;height:9px;border-radius:50%;background:var(--blue)}
.meta{display:flex;gap:18px;margin-top:18px;font-size:9.5px;color:var(--muted);align-items:center}
.meta span{display:flex;align-items:center;gap:5px}
.meta svg{width:11px;height:11px;fill:#9aa2aa}

/* feature tiles */
.tile{overflow:hidden}
.tile-shade{position:absolute;left:0;right:0;bottom:0;height:55%;background:linear-gradient(180deg,rgba(0,0,0,0),rgba(0,0,0,.7))}
.tile-title{position:absolute;color:var(--white);font-size:12.5px;font-weight:500;white-space:nowrap}
.tile .share-dots i{background:var(--blue)}
.tile-text{position:absolute;color:#dfe3e8;font-size:11px;line-height:19px}
.tile-text b{color:var(--blue);font-weight:500}
.tile .meta{color:var(--white)}
.tile .meta svg{fill:var(--white)}

/* newsletter */
.newsletter{left:0;top:1834px;width:1200px;height:295px;background:linear-gradient(90deg,#0b1016,#1a232d 60%,#0e141b)}
.nl-title{left:98px;top:1882px;color:var(--white);font-size:18px;font-weight:500}
.nl-text{left:98px;top:1916px;width:430px;color:#e4e8ec;font-size:13px;line-height:28px}
.nl-input{left:98px;top:1988px;width:392px;height:36px;background:var(--white);border-radius:3px;font-size:11px;color:#555;display:flex;align-items:center;padding-left:12px}
.nl-button{left:98px;top:2036px;width:145px;height:41px;background:var(--blue);border-radius:3px;color:var(--white);font-size:13px;font-weight:500;display:flex;align-items:center;justify-content:center}

/* footer */
.footer{left:0;top:2129px;width:1200px;height:272px;background:linear-gradient(180deg,#2593dc,#1578c6)}
.foot-h{color:var(--white);font-size:14px;font-weight:500}
.foot-txt{color:var(--white);font-size:11.5px;line-height:20px}
.contact-row{display:flex;align-items:flex-start;gap:14px}
.contact-row svg{width:16px;height:16px;fill:var(--white);flex:none}
.foot-date{font-style:italic;color:var(--white);font-size:11px}
.links a{display:block;color:var(--white);text-decoration:none;font-size:11.5px;line-height:27.5px}
.follow-rings{display:flex;gap:11px}
.follow-rings i{width:43px;height:43px;border:1.5px solid var(--white);border-radius:50%}
.bottom-bar{left:0;top:2401px;width:1200px;height:58px;background:#1679c4;color:var(--white);font-size:11.5px;display:flex;align-items:center;justify-content:center;border-top:1px solid rgba(255,255,255,.25)}
</style>
</head>
<body>

<!-- hero slider -->
<div class="abs hero" role="img" aria-label="Night view of historic parliament buildings and a clock tower reflected on a river"></div>
<div class="abs hero-shade"></div>
<div class="abs brand">Tandrel Brisk</div>
<div class="abs social-top"><span class="label">OUR SOCIAL NETWORKS</span><i class="ring"></i><i class="ring"></i><i class="ring"></i><i class="ring"></i></div>
<div class="abs menu">MENU <span class="menu-bars"><i></i><i></i><i></i></span></div>
<div class="abs hero-date">27 APRIL 2016</div>
<h1 class="abs hero-title">Blanditiis praesentium voluptatum..!</h1>
<p class="abs hero-text">Dignissimos ducimus qui blanditiis praesentium voluptatum deleniti atque corrupti quos dolores et quas...</p>
<div class="abs hero-by">-By Alan Merrow</div>
<div class="abs dots"><i class="on"></i><i></i><i></i></div>

<!-- categories -->
<nav class="abs cat-nav">
  <a class="active">ONLINE MEDIA BLOG</a><a>GOVERNMENT</a><a>POLITICS</a><a>COMPETITION</a><a>INVESTMENT</a>
</nav>

<svg width="0" height="0" style="position:absolute">
  <symbol id="heart" viewBox="0 0 12 12"><path d="M6 11 1.2 6.3A2.8 2.8 0 0 1 6 2.4a2.8 2.8 0 0 1 4.8 3.9Z"/></symbol>
  <symbol id="eye" viewBox="0 0 12 12"><path d="M6 2.5C3 2.5 1 6 1 6s2 3.5 5 3.5S11 6 11 6 9 2.5 6 2.5Zm0 5.5a2 2 0 1 1 0-4 2 2 0 0 1 0 4Z"/></symbol>
  <symbol id="share" viewBox="0 0 12 12"><circle cx="9.5" cy="2.5" r="2"/><circle cx="2.5" cy="6" r="2"/><circle cx="9.5" cy="9.5" r="2"/><path d="M2.5 6 9.5 2.5M2.5 6l7 3.5" stroke="#9aa2aa" stroke-width="1.2"/></symbol>
</svg>

<!-- row 1 -->
<article class="abs card" style="left:98px;top:631px;width:317px;height:429px">
  <div class="card-media" role="img" aria-label="Smiling man working on a laptop in a bright office" style="background:linear-gradient(135deg,#c9c4b9,#8e96a0 60%,#e8e6e1)"></div>
  <div class="date-tag" style="left:0;top:202px">17 APRIL 2016</div>
  <div class="card-body" style="top:254px">
    <h3 class="card-title">Accusamus et iusto odio dignissimosers ipsum...</h3>
    <p class="card-text">Sed ut perspiciatis unde omnis iste natus error sit ipsa quae ab illo inventore veritatis et quasi Nemo enim ipsam voluptatem quia voluptas...</p>
    <div class="share-dots"><i></i><i></i><i></i><i></i><i></i></div>
    <div class="meta"><span><svg><use href="#heart"/></svg>LIKES</span><span><svg><use href="#eye"/></svg>VIEWS</span><span><svg><use href="#share"/></svg>SHARE</span></div>
  </div>
</article>
<article class="abs card" style="left:442px;top:631px;width:317px;height:429px">
  <div class="card-media" role="img" aria-label="Woman thinking at a desk in front of a laptop" style="background:linear-gradient(135deg,#7a6a5a,#b8a898 50%,#e9e6e2)"></div>
  <div class="date-tag" style="left:0;top:202px">18 APRIL 2016</div>
  <div class="card-body" style="top:254px">
    <h3 class="card-title">Accusamus et iusto odio dignissimosers ipsum...</h3>
    <p class="card-text">Sed ut perspiciatis unde omnis iste natus error sit ipsa quae ab illo inventore veritatis et quasi Nemo enim ipsam voluptatem quia voluptas...</p>
    <div class="share-dots"><i></i><i></i><i></i><i></i><i></i></div>
    <div class="meta"><span><svg><use href="#heart"/></svg>LIKES</span><span><svg><use href="#eye"/></svg>VIEWS</span><span><svg><use href="#share"/></svg>SHARE</span></div>
  </div>
</article>
<article class="abs card" style="left:783px;top:631px;width:317px;height:429px">
  <div class="card-media" role="img" aria-label="Laptop with floating digital screens in a dark room" style="background:linear-gradient(135deg,#1d2a38,#4b6a86 55%,#15202b)"></div>
  <div class="date-tag" style="left:0;top:202px">19 APRIL 2016</div>
  <div class="card-body" style="top:254px">
    <h3 class="card-title">Accusamus et iusto odio dignissimosers ipsum...</h3>
    <p class="card-text">Sed ut perspiciatis unde omnis iste natus error sit ipsa quae ab illo inventore veritatis et quasi Nemo enim ipsam voluptatem quia voluptas...</p>
    <div class="share-dots"><i></i><i></i><i></i><i></i><i></i></div>
    <div class="meta"><span><svg><use href="#heart"/></svg>LIKES</span><span><svg><use href="#eye"/></svg>VIEWS</span><span><svg><use href="#share"/></svg>SHARE</span></div>
  </div>
</article>

<!-- feature row -->
<article class="abs tile" style="left:98px;top:1090px;width:661px;height:451px" role="img" aria-label="Three colleagues discussing work at a computer screen">
  <div class="abs" style="inset:0;background:linear-gradient(120deg,#3a3f46,#8d939b 45%,#d6d9dc 75%,#a9b0b7)"></div>
  <div class="tile-shade"></div>
  <div class="date-tag" style="left:0;top:0">18 APRIL 2016</div>
  <div class="tile-title" style="left:28px;top:1458px;top:368px">Sed ut perspiciatis unde omnis iste natus &nbsp;sit voluptatem doloremque...</div>
  <div class="share-dots" style="position:absolute;left:450px;top:361px;margin:0"><i></i><i></i><i></i><i></i><i></i></div>
  <p class="tile-text" style="left:28px;top:394px;width:420px">Accusantium doloremque laudantium, totam rem aperiam, eaque ipsa quae ab illo inventore veritatis et quasi architecto beatae... <b>Read More +</b></p>
  <div class="meta" style="position:absolute;left:447px;top:398px;margin:0"><span><svg><use href="#heart"/></svg>LIKES</span><span><svg><use href="#eye"/></svg>VIEWS</span><span><svg><use href="#share"/></svg>SHARE</span></div>
</article>
<article class="abs tile" style="left:783px;top:1090px;width:317px;height:213px" role="img" aria-label="Two people reviewing documents together at a desk">
  <div class="abs" style="inset:0;background:linear-gradient(135deg,#d9dcdf,#9aa0a6 55%,#5e636a)"></div>
  <div class="tile-shade"></div>
  <div class="date-tag" style="left:0;top:0">20 APRIL 2016</div>
  <div class="tile-title" style="left:21px;top:162px;font-size:11.5px">Sed ut perspiciatis unde omnis iste natusue...</div>
  <div class="share-dots" style="position:absolute;left:24px;top:189px;margin:0"><i></i><i></i><i></i><i></i><i></i></div>
</article>
<article class="abs tile" style="left:783px;top:1328px;width:317px;height:213px" role="img" aria-label="Older couple reading together on a garden bench">
  <div class="abs" style="inset:0;background:linear-gradient(135deg,#4e6b3a,#8fa46e 50%,#3d4e30)"></div>
  <div class="tile-shade"></div>
  <div class="date-tag" style="left:0;top:0">19 APRIL 2016</div>
  <div class="tile-title" style="left:21px;top:162px;font-size:11.5px">Sed ut perspiciatis unde omnis iste natusue...</div>
  <div class="share-dots" style="position:absolute;left:24px;top:189px;margin:0"><i></i><i></i><i></i><i></i><i></i></div>
</article>

<!-- row 3 -->
<article class="abs card" style="left:98px;top:1572px;width:317px;height:231px">
  <div class="date-tag" style="left:0;top:0">12 APRIL 2016</div>
  <div class="card-body" style="top:55px">
    <h3 class="card-title">Accusamus et iusto odio dignissimosers ipsum...</h3>
    <p class="card-text">Sed ut perspiciatis unde omnis iste natus error sit ipsa quae ab illo inventore veritatis et quasi Nemo enim ipsam voluptatem quia voluptas...</p>
    <div class="share-dots"><i></i><i></i><i></i><i></i><i></i></div>
    <div class="meta"><span><svg><use href="#heart"/></svg>LIKES</span><span><svg><use href="#eye"/></svg>VIEWS</span><span><svg><use href="#share"/></svg>SHARE</span></div>
  </div>
</article>
<article class="abs card" style="left:442px;top:1572px;width:317px;height:231px">
  <div class="date-tag" style="left:0;top:0">12 APRIL 2016</div>
  <div class="card-body" style="top:55px">
    <h3 class="card-title">Accusamus et iusto odio dignissimosers ipsum...</h3>
    <p class="card-text">Sed ut perspiciatis unde omnis iste natus error sit ipsa quae ab illo inventore veritatis et quasi Nemo enim ipsam voluptatem quia voluptas...</p>
    <div class="share-dots"><i></i><i></i><i></i><i></i><i></i></div>
    <div class="meta"><span><svg><use href="#heart"/></svg>LIKES</span><span><svg><use href="#eye"/></svg>VIEWS</span><span><svg><use href="#share"/></svg>SHARE</span></div>
  </div>
</article>
<article class="abs card" style="left:783px;top:1572px;width:317px;height:231px">
  <div class="date-tag" style="left:0;top:0">12 APRIL 2016</div>
  <div class="card-body" style="top:55px">
    <h3 class="card-title">Accusamus et iusto odio dignissimosers ipsum...</h3>
    <p class="card-text">Sed ut perspiciatis unde omnis iste natus error sit ipsa quae ab illo inventore veritatis et quasi Nemo enim ipsam voluptatem quia voluptas...</p>
    <div class="share-dots"><i></i><i></i><i></i><i></i><i></i></div>
    <div class="meta"><span><svg><use href="#heart"/></svg>LIKES</span><span><svg><use href="#eye"/></svg>VIEWS</span><span><svg><use href="#share"/></svg>SHARE</span></div>
  </div>
</article>

<!-- newsletter -->
<section class="abs newsletter" role="img" aria-label="Dark night skyline of a city with a domed cathedral"></section>
<h2 class="abs nl-title">SIGN UP OUR NEWSLETTER</h2>
<p class="abs nl-text">Sign up to our email briefings to have the best of Tandrel Brisk delivered direct to your inbox.</p>
<div class="abs nl-input">Enter Your e-Mail Address</div>
<div class="abs nl-button">SUBSCRIBE</div>

<!-- footer -->
<footer class="abs footer"></footer>
<div class="abs" style="left:98px;top:2170px;width:240px">
  <h4 class="foot-h">CONTACT US</h4>
  <div class="contact-row foot-txt" style="margin-top:28px"><svg viewBox="0 0 16 16"><path d="M4 1h3l1 4-2 1.5a9 9 0 0 0 3.5 3.5L11 8l4 1v3c0 1-1 2-2 2A12 12 0 0 1 2 3c0-1 1-2 2-2Z"/></svg>(+111) 888 - 8888 (Phone)</div>
  <div class="contact-row foot-txt" style="margin-top:14px"><svg viewBox="0 0 16 16"><path d="M4 1h8v4H4zM1 6h14v7h-3v2H4v-2H1zm4 5v3h6v-3z"/></svg>(000)-121-1231 &nbsp;(Fax)</div>
  <div class="contact-row foot-txt" style="margin-top:12px"><svg viewBox="0 0 16 16"><path d="M1 3h14v10H1zm1.5 1.5L8 9l5.5-4.5"/></svg><span style="text-decoration:underline">admin@tandrelbrisk.com</span></div>
  <div class="contact-row foot-txt" style="margin-top:10px"><svg viewBox="0 0 16 16"><path d="M8 1a5 5 0 0 1 5 5c0 4-5 9-5 9S3 10 3 6a5 5 0 0 1 5-5Zm0 3a2 2 0 1 0 0 4 2 2 0 0 0 0-4Z"/></svg>PO Box 9101, lorem Ipsum<br>Dummy Text</div>
</div>
<div class="abs" style="left:372px;top:2170px;width:260px">
  <h4 class="foot-h">POPULAR POST</h4>
  <p class="foot-txt" style="margin-top:24px">Sed ut perspiciatis unde omnis iste natus error sit voluptatem accusantium doloremque</p>
  <p class="foot-date" style="margin-top:4px">22 April 2016</p>
  <p class="foot-txt" style="margin-top:14px">Sed ut perspiciatis unde omnis iste natus error sit voluptatem accusantium doloremque</p>
  <p class="foot-date" style="margin-top:4px">22 April 2016</p>
</div>
<div class="abs links" style="left:701px;top:2170px">
  <h4 class="foot-h" style="margin-bottom:16px">QUICK LINKS</h4>
  <a>Home</a><a>Recent blog</a><a>Terms &amp; Conditions</a><a>Privacy policy</a><a>Site Map</a><a>Contact us</a>
</div>
<div class="abs" style="left:887px;top:2170px;width:220px">
  <h4 class="foot-h">FOLLOW US</h4>
  <p class="foot-txt" style="margin-top:22px;font-size:11px;line-height:21px">Lorem ipsum dolor sit amet, consectetur adipiscing elit. Nulla in purus nibh. Donec ornare felis neque. Nullam tortor!</p>
  <div class="follow-rings" style="margin-top:28px"><i></i><i></i><i></i><i></i></div>
</div>
<div class="abs bottom-bar">© COPY RIGHT2016 TANDREL BRISK. ALL &nbsp;RIGHTS RESERVED</div>

</body>
</html>
```